CREATE A BUSINESS CARD FOR A BOAT CLEANING SERVICE

WE ARE STARTING A NEW BOAT CLEANING BUSINESS. WE DIVE UNDERWATER TO CLEAN BOAT HULLS, JETTIES, UNDERWATER STRUCTURES ETC. WE ARE LOOKING FOR AN UPPERMARKET MODERN LOGO AND BUSINESS CARD AS ALOT OF OUR TARGET MARKET WILL BE HIGH END. YOU HAVE TO DESIGN A BUSINESS CARD AND LOGO SEPERATELY .
THE BUSINESS CARD DIMESNION MUST BE STANDARD SIZE.
The standard dimensions of a printed business card are 3.5 x 2 inches

Target Market(s)

UNDERWATER SERVICED

Industry/Entity Type

Business

Contact Information for Business Card

HOLLAND UNDERWATER SERVICES

Font styles to use
Serif

Colors

Designer to choose colors to be used in the design.

Requirements
Must have
• HOLLAND
Nice to have
• dark
Should not have
• more than 3 colors

```html
<!DOCTYPE html>
<html lang="en">
<head>
<meta charset="utf-8">
<title>Holland Underwater Services – Business Card</title>
<link rel="stylesheet" href="https://fonts.googleapis.com/css2?family=Source+Sans+3:wght@400;600&display=swap">
<style>
  :root {
    --navy: #16528c;
    --grey-band: #a7a8aa;
    --white: #ffffff;
    --stage: #e9ebee;
    --pattern-light: #1d5e9b;
  }
  * { box-sizing: border-box; margin: 0; padding: 0; }
  html, body { width: 1200px; height: 900px; overflow: hidden; }
  body {
    background: var(--stage);
    font-family: "Source Sans 3", sans-serif;
    position: relative;
  }
  .card {
    position: absolute;
    overflow: hidden;
    box-shadow: 0 4px 14px rgba(0,0,0,0.18);
  }

  /* Front */
  .card-front {
    left: 177px; top: 73px; width: 589px; height: 365px;
    background: var(--white);
  }
  .front-bands { position: absolute; inset: 0; }
  .brand {
    position: absolute; left: 120px; top: 62px;
    display: flex; align-items: center; gap: 22px;
    color: var(--navy); font-weight: 600;
  }
  .brand-dot {
    width: 58px; height: 58px; border-radius: 50%;
    background: var(--navy);
  }
  .brand-name { font-size: 62px; line-height: 0.9; letter-spacing: 0.5px; }
  .brand-tagline { font-size: 17px; letter-spacing: 2.6px; margin-top: 6px; }

  .person {
    position: absolute; right: 326px; top: 256px;
    text-align: right; color: var(--white);
  }
  .person-name { font-size: 20px; font-weight: 600; line-height: 1.1; }
  .person-role { font-size: 16px; font-weight: 400; margin-top: 3px; }

  .contact-list {
    position: absolute; left: 293px; top: 247px;
    list-style: none; color: var(--white); font-size: 16px;
  }
  .contact-list li { display: flex; align-items: center; gap: 6px; height: 22px; }
  .contact-list svg { width: 11px; height: 11px; fill: var(--white); }

  .address {
    position: absolute; left: 91px; top: 320px;
    color: var(--white); font-size: 16px;
  }

  /* Back */
  .card-back {
    left: 388px; top: 505px; width: 567px; height: 352px;
    background: var(--navy);
  }
  .back-texture {
    position: absolute; inset: 0;
    background: linear-gradient(135deg, var(--navy) 0%, var(--pattern-light) 55%, var(--navy) 100%);
  }
  .back-brand {
    position: absolute; left: 140px; top: 132px;
    color: var(--white); font-weight: 600; text-align: left;
  }
  .back-brand .brand-name { font-size: 68px; line-height: 0.9; }
  .back-brand .brand-tagline { font-size: 18px; letter-spacing: 2.4px; margin-top: 4px; }
</style>
</head>
<body>

<section class="card card-front" aria-label="Business card front">
  <svg class="front-bands" width="589" height="365" viewBox="0 0 589 365" aria-hidden="true">
    <polygon points="0,189 405,189 383,215 0,215" fill="var(--grey-band)"/>
    <polygon points="416,182 589,182 589,365 0,365 0,219 385,219" fill="var(--navy)"/>
  </svg>

  <div class="brand">
    <span class="brand-dot"></span>
    <div>
      <div class="brand-name">HOLLAND</div>
      <div class="brand-tagline">UNDERWATER SERVICES</div>
    </div>
  </div>

  <div class="person">
    <div class="person-name">PETER MARSH</div>
    <div class="person-role">Managing Director</div>
  </div>

  <ul class="contact-list">
    <li>
      <svg viewBox="0 0 24 24"><path d="M6.6 10.8a15.1 15.1 0 0 0 6.6 6.6l2.2-2.2a1 1 0 0 1 1-.25 11.4 11.4 0 0 0 3.6.57 1 1 0 0 1 1 1V20a1 1 0 0 1-1 1A17 17 0 0 1 3 4a1 1 0 0 1 1-1h3.5a1 1 0 0 1 1 1c0 1.25.2 2.45.57 3.6a1 1 0 0 1-.25 1z"/></svg>
      044-987 654 321
    </li>
    <li>
      <svg viewBox="0 0 24 24"><path d="M2 5h20v14H2z M2 5l10 7 10-7" /></svg>
      info@hollanddive.com
    </li>
    <li>
      <svg viewBox="0 0 24 24"><circle cx="12" cy="12" r="10"/><path d="M2 12h20M12 2c3 3 3 17 0 20M12 2c-3 3-3 17 0 20" stroke="var(--navy)" stroke-width="1.6" fill="none"/></svg>
      www.hollanddive.com
    </li>
  </ul>

  <p class="address">48 Harbour Quay, Marina Point, Seaview, 204718.</p>
</section>

<section class="card card-back" aria-label="Business card back">
  <div class="back-texture" role="img" aria-label="Repeating faint brand-symbol texture across the back of the card"></div>
  <div class="back-brand">
    <div class="brand-name">HOLLAND</div>
    <div class="brand-tagline">UNDERWATER SERVICES</div>
  </div>
</section>

</body>
</html>
```